Brightfield Ventures Inc. Letterhead

Creation of attractive and eye catching letterhead for a business start-up for the construction industry. Letterhead must relate to construction, but avoid standard hammer and tools in the design.

I forgot to add some details, sorry about that. Some pertinent info: Ph: 916-555-0187 brightfieldventures.example 448 Willowmere Ave, Ste 210 Folsom, CA 95999 info@brightfieldventures.example not sure if slogan should be in there" “Connecting construction professionals to create a purpose driven industry.” must be able to be used in word. Thanks!

```html
<!DOCTYPE html>
<html lang="en">
<head>
<meta charset="utf-8">
<title>Brightfield Ventures Inc. Letterhead</title>
<link href="https://fonts.googleapis.com/css2?family=Montserrat:wght@600;700&family=Open+Sans:wght@400;600;700&display=swap" rel="stylesheet">
<style>
  :root {
    --navy: #1b2a5e;
    --red: #c8141b;
    --ink: #2b2b2b;
    --muted: #555a66;
    --paper: #ffffff;
    --backdrop: #e9eaec;
  }
  * { box-sizing: border-box; margin: 0; padding: 0; }
  html, body { width: 1200px; height: 784px; overflow: hidden; background: var(--backdrop); }
  .canvas { position: relative; width: 1200px; height: 784px; }
  .letterhead {
    position: absolute; left: 330px; top: 12px; width: 540px; height: 760px;
    background: var(--paper); box-shadow: 0 2px 10px rgba(0,0,0,.12);
    font-family: "Open Sans", Arial, sans-serif; color: var(--ink);
    overflow: hidden;
  }
  .brand {
    position: absolute; left: 44px; top: 46px;
    display: flex; align-items: center; gap: 8px;
    padding-bottom: 6px; border-bottom: 1px solid var(--red);
  }
  .brand-mark { width: 12px; height: 12px; background: var(--red); }
  .brand-name {
    font-family: "Montserrat", Arial, sans-serif; font-weight: 700;
    font-size: 15px; letter-spacing: .06em; text-transform: uppercase; color: var(--navy);
  }
  .letter-body { position: absolute; left: 44px; top: 130px; width: 420px; }
  .salutation { font-weight: 700; font-size: 12px; color: var(--ink); margin-bottom: 14px; }
  .letter-body p { font-size: 10.5px; line-height: 1.55; margin-bottom: 14px; color: var(--ink); }
  .signature {
    width: 120px; height: 54px; margin-top: 10px;
    background: linear-gradient(90deg, #e4e4e4, #f4f4f4); border-radius: 4px;
  }
  .footer-band {
    position: absolute; left: 0; right: 0; bottom: 0; height: 8px; background: var(--navy);
  }
  .footer-contact {
    position: absolute; left: 44px; bottom: 22px; right: 44px;
    display: flex; justify-content: space-between; align-items: flex-end;
    font-size: 9.5px; line-height: 1.6; color: var(--muted);
  }
  .contact-lines { list-style: none; }
  .contact-lines li { display: flex; align-items: center; gap: 5px; }
  .contact-icon { width: 10px; height: 10px; flex: none; }
  .web-tab {
    position: absolute; right: 0; bottom: 8px; height: 24px; padding: 0 16px 0 22px;
    background: var(--red); color: #fff; font-size: 9.5px; line-height: 24px;
    clip-path: polygon(12px 0, 100% 0, 100% 100%, 0 100%);
  }
  .footer-contact { bottom: 44px; }
</style>
</head>
<body>
<div class="canvas">
  <article class="letterhead">
    <header class="brand">
      <span class="brand-mark"></span>
      <span class="brand-name">Brightfield Ventures Inc.</span>
    </header>

    <section class="letter-body">
      <p class="salutation">Dear Mr. Harlan,</p>
      <p>Lorem Ipsum is simply dummy text of the printing and typesetting industry. Lorem Ipsum has been the industry's standard dummy text ever since the 1500s, when an unknown printer took a galley of type and scrambled it to make a type specimen book. It has survived not only five centuries, but also the leap into electronic typesetting, remaining essentially unchanged.</p>
      <p>The standard chunk of Lorem Ipsum used since the 1500s is reproduced below for those interested. Sections 1.10.32 and 1.10.33 from "de Finibus Bonorum et Malorum" by Cicero are also reproduced in their exact original form, accompanied by English versions from the 1914 translation by H. Rackham.</p>
      <p>Lorem Ipsum is simply dummy text of the printing and typesetting industry. Lorem Ipsum has been the industry's standard dummy text ever since the 1500s, when an unknown printer took a galley of type and scrambled it to make a type specimen book. It has survived not only five centuries, but also the leap into electronic typesetting, remaining essentially unchanged. It was popularised in the</p>
      <p>The standard chunk of Lorem Ipsum used since the 1500s is reproduced below for those interested. Sections 1.10.32 and 1.10.33 from "de Finibus Bonorum et Malorum" by Cicero are also reproduced in their exact original form, accompanied by English versions from the 1914 translation by H. Rackham.</p>
      <div class="signature" role="img" aria-label="Handwritten signature"></div>
    </section>

    <footer>
      <div class="footer-contact">
        <address class="contact-address" style="font-style:normal">
          448 Willowmere Ave, Ste 210,<br>Folsom, CA 95999
        </address>
        <ul class="contact-lines">
          <li>
            <svg class="contact-icon" viewBox="0 0 10 10" aria-hidden="true"><circle cx="5" cy="5" r="5" fill="var(--red)"/><path d="M3.2 2.6l1 1-.5.6c.4.8.9 1.3 1.6 1.6l.6-.5 1 1-.6.9C4.6 7 3 5.4 2.8 3.2z" fill="#fff"/></svg>
            916-555-0187
          </li>
          <li>
            <svg class="contact-icon" viewBox="0 0 10 10" aria-hidden="true"><circle cx="5" cy="5" r="5" fill="var(--red)"/><rect x="2.5" y="3.3" width="5" height="3.4" fill="none" stroke="#fff" stroke-width=".8"/><path d="M2.5 3.3L5 5.3 7.5 3.3" fill="none" stroke="#fff" stroke-width=".8"/></svg>
            info@brightfieldventures.example
          </li>
        </ul>
      </div>
      <div class="web-tab">www.brightfieldventures.example</div>
      <div class="footer-band"></div>
    </footer>
  </article>
</div>
</body>
</html>
```